Pinecrest Harbor Foundation Web Design

The design we need is for a WordPress blog that will be our content platform. We are a registered 501(c)3 non-profit that focuses on financially supporting the treatment of cancer patients that have been told they have no hope and there is nothing the conventional medical system can do for them. Through this wesbite we want to both rasie awareness about the treatment options plus, raise funds for treating patients. The two primary target audiences of the site are...

1. Terminally ill patients and their families to let them know that there is an option other then hospice and that we are hear to support that option.

2. People looking to help donate to a worthwhile cause that resonates with them.

The website is https://pinecrestharborfoundation.org/

See attached logo designs!!!

Target Market(s)

Cancer patients and their families

Industry/Entity Type

Foundation

Font styles to use
Sans Serif

Colors
ffffff
fbed22

Requirements
Must have
• I like this look of this site. It is clean, simple, helpful, soft. I like the flow of the pages.
• http://www.meadowsforcalm.org/
• I like the design and flow but NOT the color or boldness
• https://tvbn-youth.org/
• I like this style for a donation page.
• https://www.tumorstudyhub.org/we-are-tsh/join-the-cause/donations/one-time-donation
• with the addition of a Would you like your employer to match? button.
Nice to have
• White black and gold - but soft
• Even possibly grayscale like the site I like.

```html
<!DOCTYPE html>
<html lang="en">
<head>
<meta charset="utf-8">
<title>Pinecrest Harbor Foundation</title>
<link href="https://fonts.googleapis.com/css2?family=Open+Sans:wght@300;400;600&family=Oswald:wght@400;500&display=swap" rel="stylesheet">
<style>
  :root{
    --gold:#efc84f;
    --gold-soft:#f3d36f;
    --ink:#1d1d1d;
    --text:#555;
    --muted:#777;
    --white:#fff;
    --nav-top:#c9c9c9;
    --nav-bottom:#9d9d9d;
    --footer:#eef0f3;
    --rule:#e3e3e3;
  }
  *{box-sizing:border-box;margin:0;padding:0}
  html,body{width:670px;height:1200px;overflow:hidden;background:var(--white)}
  body{position:relative;font-family:"Open Sans",Arial,sans-serif;color:var(--ink)}
  .abs{position:absolute}

  /* header */
  .brand{left:51px;top:16px;display:flex;align-items:center;gap:6px}
  .brand-dot{width:14px;height:14px;border-radius:50%;background:var(--gold)}
  .brand-name{font-size:11px;font-weight:600;color:var(--ink);line-height:1.1;width:110px}
  .contact-item{display:flex;align-items:center;gap:8px;top:16px}
  .contact-icon{width:28px;height:28px;border:1px solid #999;border-radius:50%;display:flex;align-items:center;justify-content:center}
  .contact-label{font-size:10px;color:#888;line-height:1.3}
  .contact-value{font-size:8px;color:#333}
  .btn{background:var(--gold);color:var(--white);border-radius:12px;font-size:9px;display:inline-block;text-align:center}
  .header-btn{left:545px;top:20px;width:75px;height:19px;line-height:19px}

  /* nav */
  .nav{left:0;top:62px;width:670px;height:28px;background:linear-gradient(var(--nav-top),var(--nav-bottom));display:flex;padding-left:50px}
  .nav a{color:var(--white);font-size:10px;text-decoration:none;height:28px;line-height:28px;padding:0 16px;margin-right:12px}
  .nav a.active{background:var(--gold);padding:0 16px}

  /* hero */
  .hero{left:0;top:90px;width:670px;height:310px;background:linear-gradient(90deg,#9aa0a6,#b9bdc1 45%,#8f959b)}
  .hero-photo{right:0;top:0;width:250px;height:310px;background:linear-gradient(180deg,#a7a9ab,#8c6f78 60%,#6f4a58)}
  .hero-title{left:53px;top:118px;font-family:"Oswald",Arial,sans-serif;font-size:25px;font-weight:500;color:var(--white);letter-spacing:.2px}
  .hero-sub{left:54px;top:151px;width:360px;font-size:14px;font-weight:300;color:var(--white);line-height:22px}
  .hero-arrows{left:55px;top:210px;display:flex;gap:3px}
  .hero-arrows span{width:12px;height:12px;border-radius:50%;background:#555;display:flex;align-items:center;justify-content:center}

  /* welcome */
  .section-title{width:670px;text-align:center;font-size:18px;color:var(--ink)}
  .welcome-title{top:438px}
  .welcome-text{left:88px;top:473px;width:494px;text-align:center;font-size:7.5px;line-height:15px;color:var(--text)}
  .feature{width:180px;text-align:center;top:547px}
  .feature-icon{width:58px;height:58px;border-radius:50%;background:var(--gold);margin:0 auto;box-shadow:0 3px 3px rgba(0,0,0,.12);display:flex;align-items:center;justify-content:center}
  .feature h3{font-weight:400;font-size:13px;margin-top:10px}
  .feature p{font-size:7px;line-height:13px;color:var(--text);margin-top:4px;padding:0 20px}
  .feature .more{font-size:7px;color:#333;margin-top:3px}
  .divider{left:51px;top:720px;width:570px;height:1px;background:var(--rule)}

  /* what we do */
  .what-title{top:756px}
  .card{width:178px;top:802px}
  .card-photo{width:178px;height:108px;border:3px solid #f2f2f2;box-shadow:0 0 2px rgba(0,0,0,.2)}
  .card h4{font-weight:400;font-size:9.5px;margin-top:10px;color:#333}
  .card p{font-size:7px;line-height:12px;color:var(--muted);margin-top:4px}
  .card .more{font-size:6.5px;color:#333;margin-top:5px}

  /* footer */
  .footer{left:0;top:1027px;width:670px;height:173px;background:var(--footer)}
  .footer-brand{left:61px;top:1055px;display:flex;align-items:center;gap:6px}
  .social{left:54px;top:1108px;display:flex;gap:7px}
  .social span{width:18px;height:18px;border-radius:50%;background:var(--white);box-shadow:0 1px 3px rgba(0,0,0,.25)}
  .footer-heading{font-size:8.5px;color:#333}
  .footer-list{font-size:7px;color:#555;line-height:12px}
  .footer-list li{list-style:none;display:flex;gap:7px;margin-bottom:4px}
  .footer-rule{left:51px;top:1160px;width:570px;height:1px;background:#c9ccd0}
  .copyright{left:0;top:1177px;width:670px;text-align:center;font-size:6.5px;color:#333}
</style>
</head>
<body>

<header>
  <div class="abs brand"><span class="brand-dot"></span><span class="brand-name">Pinecrest Harbor Foundation</span></div>
  <div class="abs contact-item" style="left:291px">
    <span class="contact-icon"><svg width="12" height="12" viewBox="0 0 24 24"><path d="M6.6 10.8a15 15 0 006.6 6.6l2.2-2.2c.3-.3.7-.4 1-.2 1.1.4 2.3.6 3.6.6.6 0 1 .4 1 1V20c0 .6-.4 1-1 1A17 17 0 013 4c0-.6.4-1 1-1h3.5c.6 0 1 .4 1 1 0 1.3.2 2.5.6 3.6.1.3 0 .7-.2 1z" fill="#666"/></svg></span>
    <div><div class="contact-label">Phone</div><div class="contact-value">+32 (0)2 418 5091</div></div>
  </div>
  <div class="abs contact-item" style="left:412px">
    <span class="contact-icon"><svg width="12" height="10" viewBox="0 0 24 18"><rect x="1" y="1" width="22" height="16" rx="2" fill="#666"/><path d="M2 3l10 7 10-7" stroke="#fff" stroke-width="2" fill="none"/></svg></span>
    <div><div class="contact-label">Email</div><div class="contact-value">hello@pinecrestharbor.org</div></div>
  </div>
  <a class="abs btn header-btn">Donate Now</a>
</header>

<nav class="abs nav">
  <a class="active">Home</a><a>About us</a><a>Services</a><a>Blog</a><a>Support</a><a>Faq</a><a>Contact Us</a>
</nav>

<section class="abs hero">
  <div class="abs hero-photo" role="img" aria-label="Photo of a smiling woman in a scarf and cardigan"></div>
  <h1 class="abs hero-title">PINECREST HARBOR FOUNDATION</h1>
  <p class="abs hero-sub">Non-profit that focuses on financially supporting the treatment of cancer patients</p>
  <div class="abs hero-arrows">
    <span><svg width="6" height="6" viewBox="0 0 6 6"><path d="M4 1L2 3l2 2" stroke="#fff" fill="none"/></svg></span>
    <span><svg width="6" height="6" viewBox="0 0 6 6"><path d="M2 1l2 2-2 2" stroke="#fff" fill="none"/></svg></span>
  </div>
</section>

<section>
  <h2 class="abs section-title welcome-title" style="font-weight:400">Welcome To Pinecrest Harbor Foundation</h2>
  <p class="abs welcome-text">It is a long established fact that a reader will be distracted by the readable content of a page when looking at its layout. The point of using Lorem Ipsum is that it has a more-or-less normal distribution of letters, as opposed to using 'Content here, content here', making it look like readable English. Many desktop publishing packages</p>

  <div class="abs feature" style="left:67px">
    <div class="feature-icon"><svg width="24" height="20" viewBox="0 0 24 20"><circle cx="12" cy="6" r="4" fill="#fff"/><circle cx="4.5" cy="8" r="3" fill="#fff"/><circle cx="19.5" cy="8" r="3" fill="#fff"/><path d="M5 20a7 7 0 0114 0z" fill="#fff"/><path d="M0 18a4.5 4.5 0 018-2v4H0zM24 18a4.5 4.5 0 00-8-2v4h8z" fill="#fff"/></svg></div>
    <h3>Dolorem Ipsum</h3>
    <p>It is a long established fact that a reader will be distracted by the readable</p>
    <div class="more">Learn More -&gt;</div>
  </div>
  <div class="abs feature" style="left:246px">
    <div class="feature-icon"><svg width="24" height="24" viewBox="0 0 24 24"><rect x="2" y="4" width="17" height="17" rx="2" stroke="#fff" stroke-width="2" fill="none"/><path d="M10 14l1-4 9-9 3 3-9 9z" fill="#fff"/></svg></div>
    <h3>Neque porro</h3>
    <p>It is a long established fact that a reader will be distracted by the readable</p>
    <div class="more">Learn More -&gt;</div>
  </div>
  <div class="abs feature" style="left:424px">
    <div class="feature-icon"><svg width="24" height="22" viewBox="0 0 24 22"><path d="M12 0L1 5h22z" fill="#fff"/><rect x="1" y="6" width="22" height="2" fill="#fff"/><rect x="3" y="9" width="3" height="8" fill="#fff"/><rect x="8" y="9" width="3" height="8" fill="#fff"/><rect x="13" y="9" width="3" height="8" fill="#fff"/><rect x="18" y="9" width="3" height="8" fill="#fff"/><rect x="0" y="18" width="24" height="3" fill="#fff"/></svg></div>
    <h3>Ipsum quia</h3>
    <p>It is a long established fact that a reader will be distracted by the readable content</p>
    <div class="more">Learn More -&gt;</div>
  </div>
</section>

<div class="abs divider"></div>

<section>
  <h2 class="abs section-title what-title" style="font-weight:400">What We Do</h2>
  <article class="abs card" style="left:51px">
    <div class="card-photo" role="img" aria-label="Photo of a counsellor taking notes with a patient on a sofa" style="background:linear-gradient(90deg,#5a4a48,#c9a79a 55%,#f2e4dc)"></div>
    <h4>Porro quisquam est</h4>
    <p>It has survived not only five centuries, but also the leap into electronic typesetting,</p>
    <div class="more">Read More »</div>
  </article>
  <article class="abs card" style="left:248px">
    <div class="card-photo" role="img" aria-label="Photo of women in a circle holding a pink awareness ribbon" style="background:linear-gradient(180deg,#d9e6ef,#eab9c6 55%,#c7d8e6)"></div>
    <h4>Dolorem ipsum quia</h4>
    <p>It has survived not only five centuries, but also the leap into electronic typesetting, remaining</p>
    <div class="more">Read More »</div>
  </article>
  <article class="abs card" style="left:446px">
    <div class="card-photo" role="img" aria-label="Photo of a woman in pink holding an awareness ribbon" style="background:linear-gradient(90deg,#f3b9cf,#e9789f 60%,#f1a6c2)"></div>
    <h4>Neque porro quisquam</h4>
    <p>It has survived not only five centuries, but also the leap into electronic typesetting, remaining</p>
    <div class="more">Read More »</div>
  </article>
</section>

<footer>
  <div class="abs footer"></div>
  <div class="abs footer-brand"><span class="brand-dot"></span><span class="brand-name">Pinecrest Harbor Foundation</span></div>
  <div class="abs social" aria-label="Social links"><span></span><span></span><span></span><span></span><span></span></div>

  <div class="abs" style="left:271px;top:1058px;width:140px">
    <div class="footer-heading">CONTACT US</div>
    <ul class="footer-list" style="margin-top:10px">
      <li><svg width="7" height="9" viewBox="0 0 10 14"><path d="M5 0a5 5 0 015 5c0 4-5 9-5 9S0 9 0 5a5 5 0 015-5z" fill="#666"/><circle cx="5" cy="5" r="2" fill="#eef0f3"/></svg><span>2450 Alder Lane, Suite 210 Portland, OR 97205</span></li>
      <li><svg width="7" height="7" viewBox="0 0 24 24"><path d="M6.6 10.8a15 15 0 006.6 6.6l2.2-2.2c.3-.3.7-.4 1-.2 1.1.4 2.3.6 3.6.6.6 0 1 .4 1 1V20c0 .6-.4 1-1 1A17 17 0 013 4c0-.6.4-1 1-1h3.5c.6 0 1 .4 1 1 0 1.3.2 2.5.6 3.6.1.3 0 .7-.2 1z" fill="#666"/></svg><span>503.555.0147</span></li>
      <li><svg width="8" height="6" viewBox="0 0 24 18"><rect x="1" y="1" width="22" height="16" rx="2" fill="#666"/></svg><span>hello@pinecrestharbor.org</span></li>
    </ul>
  </div>

  <div class="abs" style="left:474px;top:1058px;width:150px">
    <div class="footer-heading">DONATE</div>
    <p class="footer-list" style="margin-top:10px;font-size:6.5px;line-height:11px">It is a long established fact that a reader will be distracted by the readable content</p>
    <a class="btn" style="width:76px;height:19px;line-height:19px;margin-top:6px">Donate Now</a>
  </div>

  <div class="abs footer-rule"></div>
  <p class="abs copyright">Copyright © 2017. All Rights Reserved</p>
</footer>

</body>
</html>
```